Business card for denture clinic Veltrimora

We need a new business card with our new logo. We are a denture clinic in New Zealand with our target market being 45+ years old. We would need a space on the back to write our patients next appointment on. We would space for only one appointment rather than a list. We will attach a photo showing an example of this. But of course, we would like to see your twist on this. We want it to be bold and easy to read and a good mixture of professional but modern. We have attached our logo to be used on the card.

Target Market(s)

People aged 45+ needing dentures

Industry/Entity Type

Dental

Contact Information for Business Card

We want our logo on the front and the space to write an appointment on the back. I've attached an example our our old business card showing this. We need to have the technicians details on the front.

Font styles to use
Sans Serif

Colors
0255a3
919191
fbfbfb

Requirements
Must have
• The following details:
• Liam Dorsett BDT, PGDipCDentTech Calverin
• Dental Prosthetist
• Phone numbers: 0800 47 3125
• 09 572 1394
• Email: liam@veltrimora.co.nz
• www.veltrimora.co.nz
• Address: 14 Marlow Crest Road
• Halbrook West
• Auckland 0793
Nice to have
• We would like our business cards to have more than just two colours as we want them to be more vibrant. We have uploaded an example of a business card we liked that showed this.

```html
<!DOCTYPE html>
<html lang="en">
<head>
<meta charset="utf-8">
<title>Veltrimora – Business Card</title>
<link href="https://fonts.googleapis.com/css2?family=Open+Sans:ital,wght@0,300;0,400;0,600;0,700;1,400&display=swap" rel="stylesheet">
<style>
  :root {
    --blue: #0255a3;
    --blue-bright: #1a6fc4;
    --grey: #919191;
    --grey-dark: #6f6a6a;
    --paper: #fbfbfb;
    --ink: #5a5a5a;
    --stage: #e6e8eb;
  }
  * { box-sizing: border-box; margin: 0; padding: 0; }
  html, body { width: 1200px; height: 950px; overflow: hidden; }
  body {
    background: var(--stage);
    font-family: "Open Sans", Arial, sans-serif;
    display: flex; flex-direction: column; align-items: center; justify-content: center;
    gap: 60px;
  }
  .card {
    position: relative; width: 700px; height: 400px;
    border-radius: 22px; overflow: hidden;
    box-shadow: 0 6px 18px rgba(0,0,0,.15);
  }

  /* Front */
  .card--front { background: var(--paper); }
  .brand {
    position: absolute; left: 50px; top: 120px;
    display: flex; align-items: center; gap: 16px;
  }
  .brand__square { width: 54px; height: 54px; background: var(--blue-bright); border-radius: 6px; }
  .brand__name { font-size: 38px; font-weight: 400; color: var(--blue-bright); letter-spacing: 1px; text-transform: uppercase; }
  .divider { position: absolute; left: 385px; top: 40px; width: 1px; height: 250px; background: #d6d6d6; }
  .contact { position: absolute; left: 410px; top: 44px; color: var(--ink); font-size: 15px; line-height: 1.55; }
  .contact__name { color: var(--blue-bright); font-weight: 700; font-size: 19px; line-height: 1.25; }
  .contact__quals { color: var(--blue-bright); font-weight: 600; font-size: 15px; }
  .contact__role { font-weight: 300; margin-bottom: 8px; }
  .contact__line { display: flex; align-items: center; gap: 8px; }
  .contact__line svg { width: 14px; height: 14px; flex: none; }
  .contact__address { margin-top: 8px; }
  .band {
    position: absolute; left: 0; bottom: 0; width: 100%; height: 62px;
    display: flex;
  }
  .band__blue { flex: 1; background: var(--blue-bright); display: flex; align-items: center; padding-left: 230px; }
  .band__grey { width: 70px; background: var(--grey-dark); }
  .band__web { color: #fff; font-size: 17px; letter-spacing: 2px; }

  /* Back */
  .card--back { background: var(--blue-bright); }
  .card--back .brand { left: 0; right: 0; top: 48px; justify-content: center; }
  .card--back .brand__square { background: #fff; }
  .card--back .brand__name { color: #fff; }
  .appointment {
    position: absolute; left: 0; top: 170px; width: 630px; height: 190px;
    background: var(--paper); display: flex;
  }
  .appointment__row { flex: 1; padding: 0 40px; display: flex; align-items: center; }
  .appointment__cap { width: 22px; background: var(--grey-dark); }
  .slot { width: 100%; display: flex; align-items: flex-end; gap: 10px; font-style: italic; font-size: 18px; color: var(--ink); }
  .slot__fill { border-bottom: 1px dotted var(--grey); height: 22px; }
  .slot__fill--date { flex: 1.4; }
  .slot__fill--time { flex: 1; }
</style>
</head>
<body>

  <section class="card card--front" aria-label="Business card front">
    <div class="brand">
      <div class="brand__square"></div>
      <span class="brand__name">Veltrimora</span>
    </div>
    <div class="divider"></div>
    <div class="contact">
      <p class="contact__name">LIAM DORSETT BDT,</p>
      <p class="contact__quals">PGDipCDentTech Calverin</p>
      <p class="contact__role">Dental Prosthetist</p>
      <p class="contact__line">
        <svg viewBox="0 0 14 14"><path d="M3 1l2.5 3-1.5 1.5c.8 1.8 2.2 3.2 4 4L9.5 8 12.5 10.5 11 13C6 12.5 1.5 8 1 3z" fill="var(--blue-bright)"/></svg>
        0800 47 3125</p>
      <p class="contact__line">
        <svg viewBox="0 0 14 14"><rect x="2" y="1.5" width="10" height="11" fill="none" stroke="var(--blue-bright)" stroke-width="1.5"/></svg>
        09 572 1394</p>
      <p class="contact__line">
        <svg viewBox="0 0 14 14"><rect x="1" y="2" width="12" height="10" rx="1.5" fill="var(--blue-bright)"/><path d="M2 3.5l5 4 5-4" fill="none" stroke="#fff" stroke-width="1.2"/></svg>
        liam@veltrimora.co.nz</p>
      <p class="contact__address">14 Marlow Crest Road<br>Halbrook West, Auckland 0793</p>
    </div>
    <div class="band">
      <div class="band__blue"><span class="band__web">www.veltrimora.co.nz</span></div>
      <div class="band__grey"></div>
    </div>
  </section>

  <section class="card card--back" aria-label="Business card back">
    <div class="brand">
      <div class="brand__square"></div>
      <span class="brand__name">Veltrimora</span>
    </div>
    <div class="appointment">
      <div class="appointment__row">
        <div class="slot"><span class="slot__fill slot__fill--date"></span>time:<span class="slot__fill slot__fill--time"></span>am/pm</div>
      </div>
      <div class="appointment__cap"></div>
    </div>
  </section>

</body>
</html>
```